Business Cards Needed for Innovative Healthcare Marketing Company

We are a marketing company focused on healthcare. Our company is all about rebranding yourself renewing your image and generating results. The phoenix stands for "reborn" or "rising" which we provide new brands for our clients we take their old brands and renew it with creativity and innovation. I am looking for a business card with color dimension. I have attached an example of a card I think has the look and feel of what I am trying to accomplish. I like that the card example has black and grey font colors, I like the font placement and the small logo, I really like the use of the colors on the right those are the colors of my logo. My logo is phoenix so maybe incorporating flames similar to that design. I would like the back a solid color maybe red with an opaque version of the logo and website. As a marketing company I am always open to creative liberty!

Target Market(s)

Doctors and business professionals.

Industry/Entity Type

Marketing

Contact Information for Business Card

Valcorne Health Care Marketing
Marla Tenwick- CEO
#(512)638-2974
email-marla@valcorne.com
website- valcorne.com

Font styles to use
Sans Serif

Colors
ec1f27
f37122
ffc214
fbed22
fbf289
f04a50

Requirements
Must have
• The logo and required information
Nice to have
• icons by the information
Should not have
• child like font

```html
<!DOCTYPE html>
<html lang="en">
<head>
<meta charset="utf-8">
<title>Valcorne Health Care Marketing – Business Cards</title>
<link href="https://fonts.googleapis.com/css2?family=Josefin+Sans:wght@300;400&family=Open+Sans:wght@400;600&display=swap" rel="stylesheet">
<style>
  :root {
    --stage-top: #2b2b2b;
    --stage-bottom: #050505;
    --flame-top: #f4961f;
    --flame-mid: #d8592a;
    --flame-bottom: #a01f1f;
    --ink-light: #ffffff;
    --ink-red: #9b1b1e;
    --ink-red-soft: #b8352f;
    --rule-red: #d9a29f;
    --paper: #ffffff;
    --emblem-orange: #f37122;
    --emblem-gold: #ffc214;
  }
  * { margin: 0; padding: 0; box-sizing: border-box; }
  html, body { width: 1200px; height: 900px; overflow: hidden; }
  body {
    background: linear-gradient(to bottom, var(--stage-top), var(--stage-bottom));
    position: relative;
    font-family: "Open Sans", Arial, sans-serif;
  }
  .card {
    position: absolute;
    top: 306px;
    width: 439px;
    height: 271px;
    border-radius: 10px;
    overflow: hidden;
    box-shadow: 0 4px 14px rgba(0,0,0,.5);
  }
  .card--front {
    left: 149px;
    background: linear-gradient(to bottom, var(--flame-top) 0%, var(--flame-mid) 50%, var(--flame-bottom) 100%);
    color: var(--ink-light);
  }
  .card--back { left: 609px; background: var(--paper); }

  .emblem-area {
    position: absolute;
    left: 22px; top: 42px;
    width: 172px; height: 210px;
    border-radius: 50% 50% 45% 45%;
    background: radial-gradient(ellipse at 50% 55%, rgba(255,194,20,.55), rgba(160,31,31,.25) 70%, transparent 100%);
  }

  .brand { position: absolute; font-family: "Josefin Sans", Arial, sans-serif; font-weight: 300; white-space: nowrap; }
  .brand__name { display: block; letter-spacing: 0; line-height: 1; }
  .brand__rule { display: block; height: 1px; }
  .brand__tag { display: block; letter-spacing: .5px; line-height: 1; }

  .card--front .brand { left: 220px; top: 44px; width: 172px; }
  .card--front .brand__name { font-size: 32px; }
  .card--front .brand__rule { background: rgba(255,255,255,.7); margin: 6px 0 4px; }
  .card--front .brand__tag { font-size: 12.5px; }

  .person { position: absolute; left: 219px; top: 128px; }
  .person__name { font-weight: 600; font-size: 14.5px; line-height: 1.2; }
  .person__role { font-size: 11.5px; margin-top: 3px; }

  .contact { position: absolute; left: 219px; top: 183px; list-style: none; font-size: 12.5px; }
  .contact li { display: flex; align-items: center; height: 16px; }
  .contact svg { width: 10px; height: 10px; margin-right: 7px; fill: var(--ink-light); }

  .card--back .brand { left: 82px; top: 104px; color: var(--ink-red); display: flex; align-items: center; }
  .brand__mark { width: 52px; height: 52px; border-radius: 50%; background: linear-gradient(to bottom, var(--ink-red-soft), var(--emblem-orange)); margin-right: 12px; flex: none; }
  .brand__text { width: 206px; }
  .card--back .brand__name { font-size: 37px; }
  .card--back .brand__rule { background: var(--rule-red); margin: 6px 0 6px; }
  .card--back .brand__tag { font-size: 14.5px; color: var(--ink-red-soft); }
</style>
</head>
<body>
  <section class="card card--front" aria-label="Business card front">
    <div class="emblem-area" role="img" aria-label="Large flame-coloured brand emblem"></div>
    <div class="brand">
      <span class="brand__name">VALCORNE</span>
      <span class="brand__rule"></span>
      <span class="brand__tag">HEALTHCARE MARKETING</span>
    </div>
    <div class="person">
      <p class="person__name">Marla Tenwick</p>
      <p class="person__role">CEO</p>
    </div>
    <ul class="contact">
      <li><svg viewBox="0 0 10 10"><path d="M2 0.5l1.6 1.8-1 1.2a6 6 0 0 0 3.9 3.9l1.2-1L9.5 8 8.3 9.5C4 9.3.7 6 .5 1.7z"/></svg>(512)638-2974</li>
      <li><svg viewBox="0 0 10 10"><path d="M0.5 2h9v6h-9z M0.5 2l4.5 3.5L9.5 2" fill="none" stroke="#fff" stroke-width="1"/><path d="M0.5 2h9L5 5.5z"/></svg>marla@valcorne.com</li>
      <li><svg viewBox="0 0 10 10"><circle cx="5" cy="5" r="4.5"/><path d="M1 5h8M5 .5v9" stroke="#c8452a" stroke-width=".8"/></svg>valcorne.com</li>
    </ul>
  </section>

  <section class="card card--back" aria-label="Business card back">
    <div class="brand">
      <span class="brand__mark"></span>
      <div class="brand__text">
        <span class="brand__name">VALCORNE</span>
        <span class="brand__rule"></span>
        <span class="brand__tag">HEALTHCARE MARKETING</span>
      </div>
    </div>
  </section>
</body>
</html>
```